Australian Careers Business Needs 2 Banner Ad Design

We need a banner ad design for a new company based in Australia called Bright Sparrows. We provide career tools and insights to young professionals. Our target market is 20-30 year olds.

We would like to see designs that attract users on the site to click on the banner and sign up for a weekly newsletter. The newsletter will feature a blog, cheat sheets etc. Inspiration in their inbox!

The second banner is to attract users to sign up for a Pathfinder Summit. They would click on it to find out more information and then register with their email address. This convention is a 1 day workshop designed to enhance young professionals abilities to give their best at work. There will CEO insights etc.

Use of images or flash is ok. Needs to look very professional and presented in accordance to the current colour scheme in place. Visit http://www.brightsparrows-demo.com/home to understand.

Banner sizes 300 x 250.
Mandatory use of Corporate Colours required on Font.
R66 G73 B74
R242 G240 B230
R38 G128 B138

No logo necessary.

Hi All,As both banners will feature on the Bright Sparrows site there is no need for a logo or hyperlink to the site.I would like to see some better images, and a bit more creative flair.Please don't use single female images as I am wanting to avoid the women in business perception. We cater to young professionals.Some suggestions for lines to utilise on the newsletter ad:Click here for weekly career tipsInvest in your career for free hereJoin the weekly conversationWeekly career tips in your inboxSign up for our weekly newsletterSome suggestions for lines to use on the pathfinder summit ad:Register for the Pathfinder Summit - Find out how to get ahead of your peersAre you a millennial climbing the corporate ladder? Find out how to rise to the topInterested in hearing from experts who recognise millennials are our future business leaders? Click here.Thanks,Megan Added Friday, April 3, 2015

Target Market(s)

20-30 years

Industry/Entity Type

Business

Font styles to use
Sans Serif

Requirements
Must have
• Please use images in the attached as options
Should not have
• NO LOGO - Its already onsite so not needed.

```html
<!DOCTYPE html>
<html lang="en">
<head>
<meta charset="utf-8">
<title>Bright Sparrows Banner Set</title>
<link rel="stylesheet" href="https://fonts.googleapis.com/css2?family=Figtree:wght@600;700;800&family=Arimo:wght@400&display=swap">
<style>
  :root {
    --stage: #cfcdcd;
    --teal: #26808a;
    --cream: #f2f0e6;
    --slate: #42494a;
    --white: #ffffff;
    --hint: #b4b4b4;
    --gold: #e8ca80;
  }
  * { box-sizing: border-box; margin: 0; padding: 0; }
  html, body { width: 1200px; height: 900px; overflow: hidden; }
  body { background: var(--stage); position: relative; font-family: "Figtree", Arial, sans-serif; }

  .banner {
    position: absolute; width: 300px; height: 250px;
    background: var(--cream); overflow: hidden; text-align: center;
  }
  .col-1 { left: 140px; } .col-2 { left: 450px; } .col-3 { left: 760px; }
  .row-1 { top: 196px; } .row-2 { top: 454px; }

  .visual { position: absolute; left: 0; top: 0; width: 300px; height: 112px; }
  .visual--glasses { background: var(--gold); }
  .visual--coffee { background: linear-gradient(135deg, #5a4a42 0%, #8d8580 45%, #d8d4cf 70%, #6e5e54 100%); }
  .visual--mountain { background: linear-gradient(180deg, #3d4a5a 0%, #5d6878 35%, #2a2a2a 70%, #151515 100%); height: 106px; }
  .visual--crowd { background: linear-gradient(90deg, #4a4441 0%, #6a625c 40%, #9b948c 60%, #3a3532 100%); }
  .visual--team { background: linear-gradient(180deg, #d9d8d6 0%, #a9a7a4 55%, #5b5550 100%); }
  .visual--group { background: linear-gradient(90deg, #3e3530 0%, #7a6e64 45%, #c9c2b8 70%, #6b6059 100%); }

  .visual-headline {
    position: absolute; left: 0; right: 0; top: 45px; white-space: nowrap;
    font-weight: 800; font-size: 24px; line-height: 26px; color: var(--slate); letter-spacing: -0.3px;
  }
  .visual-caption {
    position: absolute; left: 22px; top: 30px; text-align: left;
    font-weight: 700; font-size: 16px; line-height: 17px; color: var(--white);
  }

  .headline { position: absolute; left: 0; right: 0; color: var(--teal); font-weight: 800; line-height: 1; white-space: nowrap; }

  .email-field {
    position: absolute; left: 20px; top: 148px; width: 261px; height: 34px;
    background: var(--white); border: 1px solid var(--teal);
    font-family: "Arimo", Arial, sans-serif; font-size: 16px; color: var(--hint);
    line-height: 32px; text-align: center;
  }
  .cta {
    position: absolute; left: 99px; width: 103px; height: 31px;
    background: var(--teal); color: var(--white);
    font-weight: 800; font-size: 16px; line-height: 31px;
  }

  .brand-name {
    position: absolute; right: 20px; top: 226px;
    color: var(--teal); font-weight: 700; font-size: 8px; line-height: 8px; letter-spacing: 0.6px; white-space: nowrap;
  }

  .tag-weekly {
    position: absolute; left: 18px; top: 219px; text-align: left;
    color: var(--teal); font-weight: 800; line-height: 1;
  }
  .tag-weekly span { display: block; }
  .tag-weekly .big { font-size: 10px; letter-spacing: 2.6px; }
  .tag-weekly .small { font-size: 6.5px; letter-spacing: 0.6px; margin-top: 1px; }
</style>
</head>
<body>

  <section class="banner col-1 row-1">
    <div class="visual visual--glasses" role="img" aria-label="Illustration of black reading glasses on a mustard background">
      <div class="visual-headline">DESPERATE TO READ?</div>
    </div>
    <p class="headline" style="top:125px;font-size:15px;">WEEKLY NEWSLETTER IS FOR YOU</p>
    <div class="email-field">Enter Your Email Here</div>
    <div class="cta" style="top:195px;">SIGN UP</div>
    <div class="brand-name">BRIGHT SPARROWS</div>
  </section>

  <section class="banner col-2 row-1">
    <div class="visual visual--coffee" role="img" aria-label="Photo of hands holding a tablet showing a newsletter beside a cup of coffee"></div>
    <p class="headline" style="top:125px;font-size:15px;">IS YOUR COFFEE TOO HOT ?</p>
    <div class="email-field">Enter Your Email Here</div>
    <div class="cta" style="top:195px;">SIGN UP</div>
    <div class="brand-name">BRIGHT SPARROWS</div>
  </section>

  <section class="banner col-3 row-1">
    <div class="visual visual--mountain" role="img" aria-label="Photo of a hand gripping a rocky mountain ledge under a stormy sky"></div>
    <p class="headline" style="top:129px;font-size:10.5px;">REST OF THE STORY WILL BE IN YOUR MAILBOX</p>
    <div class="email-field">Enter Your Email Here</div>
    <div class="cta" style="top:195px;">SIGN UP</div>
    <div class="tag-weekly"><span class="big">WEEKLY</span><span class="small">NEWSLETTER</span></div>
    <div class="brand-name">BRIGHT SPARROWS</div>
  </section>

  <section class="banner col-1 row-2">
    <div class="visual visual--crowd" role="img" aria-label="Photo of a smiling young professional in glasses at a busy event">
      <div class="visual-caption">PATHFINDER<br>SUMMIT</div>
    </div>
    <p class="headline" style="top:121px;font-size:23px;">ONE DAY WORKSHOP</p>
    <p class="headline" style="top:152px;font-size:15px;line-height:20px;">DESIGNED TO ENHANCE<br>YOUNG PROFESSIONALS</p>
    <div class="cta" style="top:195px;">MORE INFO</div>
    <div class="brand-name">BRIGHT SPARROWS</div>
  </section>

  <section class="banner col-2 row-2">
    <div class="visual visual--team" role="img" aria-label="Photo of a team of young professionals walking forward in an office"></div>
    <p class="headline" style="top:121px;font-size:23px;">ONE DAY WORKSHOP</p>
    <p class="headline" style="top:152px;font-size:9.5px;">DESIGNED TO ENHANCE YOUNG PROFESSIONALS</p>
    <div class="cta" style="top:176px;">MORE INFO</div>
    <div class="brand-name">BRIGHT SPARROWS</div>
  </section>

  <section class="banner col-3 row-2">
    <div class="visual visual--group" role="img" aria-label="Photo of a confident group of young professionals in an office"></div>
    <p class="headline" style="top:122px;font-size:19px;">ONE DAY WORKSHOP</p>
    <p class="headline" style="top:148px;font-size:9.5px;">DESIGNED TO ENHANCE</p>
    <p class="headline" style="top:160px;font-size:19px;">YOUNG PROFESSIONALS</p>
    <div class="cta" style="top:189px;">MORE INFO</div>
    <div class="brand-name">BRIGHT SPARROWS</div>
  </section>

</body>
</html>
```